Landscape Construction and Design Company

We are a landscape construction and design company from New Jersey. We design and install landscapes and hardscapes for residential properties. The name of the company is Belwick's Landscape and Design LLC. We specialize mostly in planting trees and stone work, some water features. We would like to see design themes that include a tree or trees and a stone walkway or wall. We like earth tone colors. We like traditional to modern designs.

Target Market(s)

Homeowners

Industry/Entity Type

Landscape

Contact Information for Business Card

Nature themed design, earth tone colors, space for company name, address, phone numbers, email and website address

Logo Text

No text

Font styles to use
Serif

Colors

Designer to choose colors to be used in the design.

Requirements
Must have
• A tree or trees, similar to the ones uploaded in my supporting images
Nice to have
• I like trees similar to those in my uploaded supporting images. I like artistic, nature theme, earth tone colors
Should not have
• Pictures of real landscapes, cartoon looking logo or objects

```html
<!DOCTYPE html>
<html lang="en">
<head>
<meta charset="utf-8">
<title>Belwick's Landscape and Design LLC – Business Card</title>
<link rel="stylesheet" href="https://fonts.googleapis.com/css2?family=Tinos:wght@400;700&display=swap">
<style>
  :root {
    --page: #ece6dc;
    --bark: #4a2e14;
    --bark-deep: #3a230e;
    --leaf: #a8c94a;
    --grass-light: #7aa43a;
    --grass-dark: #4d7a22;
    --water: #5aa8e0;
    --paper: #ffffff;
    --sky: #e4eaf0;
  }
  * { margin: 0; padding: 0; box-sizing: border-box; }
  html, body {
    width: 900px; height: 1200px; overflow: hidden;
    background: var(--page);
    font-family: "Tinos", "Times New Roman", serif;
  }
  .canvas { position: relative; width: 900px; height: 1200px; }

  .card {
    position: absolute;
    border-radius: 22px;
    overflow: hidden;
    box-shadow: 0 8px 18px rgba(0,0,0,.35);
  }
  .card-front {
    left: 87px; top: 137px; width: 735px; height: 428px;
    background: radial-gradient(circle at 210px 150px, #6b5a1e 0%, var(--bark) 45%, var(--bark) 100%);
  }
  .card-back {
    left: 115px; top: 633px; width: 707px; height: 429px;
    background: radial-gradient(circle at 600px 20px, #6e6420 0%, #54401a 30%, var(--bark) 60%);
  }
  .waves { position: absolute; inset: 0; }

  .brand-mark {
    position: absolute;
    display: flex; align-items: center; justify-content: center;
    border-radius: 50%;
    background: radial-gradient(circle at 50% 35%, #ffffff 0%, var(--sky) 70%);
    color: var(--bark);
    font-weight: 700;
  }
  .card-front .brand-mark { left: 95px; top: 60px; width: 220px; height: 220px; font-size: 32px; }
  .card-back .brand-mark { left: 264px; top: 80px; width: 180px; height: 180px; font-size: 27px; }

  .company { position: absolute; right: 38px; top: 14px; text-align: right; }
  .company-name { color: var(--paper); font-size: 68px; font-weight: 700; line-height: 1; }
  .company-tagline { color: var(--leaf); font-size: 20px; line-height: 1.2; }

  .person { position: absolute; right: 38px; top: 132px; text-align: right; }
  .person-name { color: var(--paper); font-size: 23px; font-weight: 700; line-height: 1.2; }
  .person-role { color: var(--leaf); font-size: 17px; line-height: 1.2; }

  .contacts { position: absolute; right: 42px; top: 280px; list-style: none; }
  .contacts li {
    display: flex; justify-content: flex-end; align-items: center; gap: 12px;
    color: var(--paper); font-size: 18.5px; height: 29.5px;
  }
  .contacts svg { width: 19px; height: 19px; fill: var(--leaf); flex: none; }

  .back-title {
    position: absolute; left: 0; right: 0; top: 276px; text-align: center;
    color: var(--paper); font-weight: 700; font-size: 25px;
  }
  .back-llc {
    position: absolute; left: 160px; right: 160px; top: 307px;
    display: flex; align-items: center; gap: 8px;
    color: var(--paper); font-weight: 700; font-size: 12px;
  }
  .back-llc::before, .back-llc::after { content: ""; flex: 1; height: 1px; background: var(--leaf); }
  .back-web {
    position: absolute; left: 0; right: 0; top: 366px; text-align: center;
    color: var(--leaf); font-size: 14px;
  }
</style>
</head>
<body>
<main class="canvas">

  <section class="card card-front">
    <svg class="waves" viewBox="0 0 735 428" preserveAspectRatio="none" aria-hidden="true">
      <defs>
        <linearGradient id="grass" x1="0" y1="0" x2="0" y2="1">
          <stop offset="0" stop-color="#86b045"/>
          <stop offset="1" stop-color="#4d7a22"/>
        </linearGradient>
      </defs>
      <path d="M0,330 C180,370 360,320 500,262 C590,228 670,214 735,212 L735,428 L0,428 Z" fill="url(#grass)"/>
      <path d="M0,318 C180,360 360,308 500,252 C590,218 670,204 735,202 L735,214 C670,216 590,232 500,266 C360,324 180,372 0,332 Z" fill="var(--bark-deep)"/>
      <path d="M0,280 C160,330 330,318 430,270 C540,215 640,195 735,190 L735,203 C640,214 560,236 480,268 C350,318 160,352 0,310 Z" fill="var(--water)"/>
      <path d="M0,362 C200,392 380,330 540,262 L560,258 C400,338 200,405 0,374 Z" fill="var(--bark-deep)" opacity=".8"/>
    </svg>

    <div class="brand-mark">Belwick's</div>

    <header class="company">
      <h1 class="company-name">Belwick's</h1>
      <p class="company-tagline">Landscape and Design LLC</p>
    </header>

    <div class="person">
      <p class="person-name">Corwin Hale</p>
      <p class="person-role">Managing Director</p>
    </div>

    <ul class="contacts">
      <li>555-201-7394
        <svg viewBox="0 0 24 24"><path d="M3 9c0-3 4-5 9-5s9 2 9 5l-4 1-1-3c-2-.6-6-.6-8 0l-1 3zM6 12h12l2 8H4z"/></svg></li>
      <li>corwinhale@mail.com
        <svg viewBox="0 0 24 24"><path d="M2 5h20v14H2zM4 7v1l8 5 8-5V7l-8 5z"/></svg></li>
      <li>www.belwicklandscape.ca
        <svg viewBox="0 0 24 24"><path d="M12 2a10 10 0 100 20 10 10 0 000-20zm0 2c1 1 2 3 2.4 6H9.6C10 7 11 5 12 4zM4.2 10h3.4c-.1 1.3-.1 2.7 0 4H4.2a8 8 0 010-4zm5.4 0h4.8c.1 1.3.1 2.7 0 4H9.6c-.1-1.3-.1-2.7 0-4zm6.8 0h3.4a8 8 0 010 4h-3.4c.1-1.3.1-2.7 0-4zM9.6 16h4.8c-.4 3-1.4 5-2.4 6-1-1-2-3-2.4-6z"/></svg></li>
      <li>Address goes here, street, Ashford, NJ-07120
        <svg viewBox="0 0 24 24"><path d="M12 2a7 7 0 00-7 7c0 5 7 13 7 13s7-8 7-13a7 7 0 00-7-7zm0 4a3 3 0 110 6 3 3 0 010-6z"/></svg></li>
    </ul>
  </section>

  <section class="card card-back">
    <div class="brand-mark">Belwick's</div>
    <h2 class="back-title">Belwick's Landscape and Design</h2>
    <p class="back-llc">LLC</p>
    <p class="back-web">www.belwicklandscape.ca</p>
  </section>

</main>
</body>
</html>
```